Maplecrest Cove Retreat Wedding and Event Venue

We are looking for a webpage for our Wedding and Event Venue just opened up in Eastern San Diego CA. It is out of a private home that has a very photogenic backyard including grapevines and orchard trees, a 15 ft waterfall into a pool and market lights hanging from trees, all connected by paved stone and compacted dirt paths

We are looking for something that will be very bright, warm and inviting to our clients. The clientele will be mostly couples between 22 and 35 years of age for the weddings and planners/executives age 22-60 for our corporate events.

We would like a rustic Outdoor look as that is what our venue showcases. You can see our facebook Here: https://www.facebook.com/MaplecrestCoveRetreat/

We would like for the pictures on the facebook to be used on the page. The google drive where most of them are located is here for full file sizes https://files.examplecloud.net/open?id=7Q-9Kpt-M2xvaT8LwQeRTp4-DN5H

We would like to see designs that go with the colors of our logo and that included stone, wood, and grapevine textures as well as anything else rustic such as Market-lights.

The final design should be welcoming for newly engaged couples and corporations/companies who would like to book an outdoor venue for their wedding or next event. There can even be a simple first page with separate tabs for weddings and events that will be able to be more specially focused to the clients.

We would also like the option to be able to edit the pictures we place on the site seasonally as we would like our pictures to reflect our clients

Target Market(s)

Engaged couples age 22-35 and corporate planners/executives age 22-60

Industry/Entity Type

Events

Font styles to use
Script

Requirements
Must have
• Rustic Look, (wood, stone, wine vines/barrels, market lights, mason jars, etc)
• tab pages/sub pages for "About us", "Packages", "Pricing", "Gallery" (we must be able to put our pictures here from all our events), "What makes us Unique", "Contact us" that we are able to enter information into
Nice to have
• Colors matching our logo, Pictures from our Facebook page (listed in brief)
Should not have
• Corporate Look

```html
<!DOCTYPE html>
<html lang="en">
<head>
<meta charset="utf-8">
<title>Maplecrest Cove Retreat – Wedding &amp; Event Venue</title>
<link href="https://fonts.googleapis.com/css2?family=Cinzel:wght@400;700&family=Roboto:wght@300;400&display=swap" rel="stylesheet">
<style>
:root{
  --wood-dark:#1c0f0a;
  --wood-mid:#3a1d12;
  --wood-warm:#5a2e1c;
  --gold:#b49a55;
  --gold-light:#cdb373;
  --cream:#f4ecd8;
  --white:#ffffff;
}
*{margin:0;padding:0;box-sizing:border-box}
html,body{width:830px;height:1200px;overflow:hidden;background:var(--wood-dark)}
.page{position:relative;width:830px;height:1200px;font-family:Arial,Helvetica,sans-serif;color:var(--white)}

/* Header */
.site-header{position:absolute;top:0;left:0;width:830px;height:153px;
  background:linear-gradient(90deg,#1a0c07 0%,#4a2416 25%,#5a2c1a 50%,#4a2416 75%,#1a0c07 100%)}
.brand{position:absolute;top:22px;left:0;width:830px;text-align:center;font-family:'Cinzel',serif}
.brand-mark{display:inline-block;width:34px;height:34px;border:1.5px solid var(--gold);border-radius:50%;margin-bottom:6px}
.brand-name{display:block;color:var(--gold);font-size:16px;letter-spacing:1px;line-height:1.1}
.brand-sub{display:block;color:var(--gold);font-size:8px;letter-spacing:4px;margin-top:2px}
.main-nav{position:absolute;top:99px;left:58px;width:714px;height:36px;
  border-top:1px dashed rgba(255,255,255,.45);border-bottom:1px dashed rgba(255,255,255,.45);
  display:flex;justify-content:space-between;align-items:center;padding:0 24px}
.main-nav a{font-family:'Cinzel',serif;font-size:9.5px;color:var(--white);text-decoration:none;letter-spacing:.5px}

/* Hero */
.hero{position:absolute;top:153px;left:0;width:830px;height:370px;
  background:radial-gradient(ellipse at 50% 45%,#8a6a66 0%,#b8aca2 45%,#ddd8cf 100%)}
.hero-photo{position:absolute;inset:0}
.hero-title{position:absolute;top:166px;left:0;width:830px;text-align:center;
  font-family:'Cinzel',serif;font-size:36px;letter-spacing:1px;color:var(--white);
  text-shadow:0 2px 6px rgba(0,0,0,.35)}
.hero-sub{position:absolute;top:216px;left:0;width:830px;text-align:center;
  font-family:'Roboto',sans-serif;font-weight:300;font-size:13px;color:var(--white)}
.hero-btn{position:absolute;top:246px;left:355px;width:120px;height:31px;border:1.5px solid var(--white);
  border-radius:16px;font-family:'Cinzel',serif;font-size:11px;color:var(--white);
  display:flex;align-items:center;justify-content:center}

/* Welcome */
.welcome{position:absolute;top:523px;left:0;width:830px;height:479px;
  background:radial-gradient(ellipse at 50% 20%,#5a2e1c 0%,#3a1d12 45%,#120805 100%)}
.welcome-heading{position:absolute;top:40px;left:0;width:830px;display:flex;justify-content:center;align-items:center;gap:6px}
.welcome-heading h2{font-family:'Cinzel',serif;font-weight:400;font-size:17px;color:var(--gold);letter-spacing:.5px}
.rule{width:54px;height:2px;background:var(--gold)}
.ornament{position:absolute;top:66px;left:360px;width:110px;height:24px;
  background:radial-gradient(ellipse,rgba(180,154,85,.55) 0%,rgba(180,154,85,0) 70%)}
.col{position:absolute;width:338px;font-size:8.4px;line-height:17.7px;text-align:justify}
.col p{margin-bottom:17.7px}
.col-left{top:112px;left:59px}
.col-right{top:112px;left:433px}
.gold-btn{display:flex;width:122px;height:36px;background:var(--gold);color:var(--white);
  font-family:'Cinzel',serif;font-size:13px;align-items:center;justify-content:center;margin-top:-1px}

/* Footer */
.site-footer{position:absolute;top:1002px;left:0;width:830px;height:198px;background:var(--gold)}
.footer-brand{position:absolute;top:18px;left:0;width:830px;text-align:center;font-family:'Cinzel',serif}
.footer-brand .brand-mark{border-color:var(--white)}
.footer-brand .brand-name,.footer-brand .brand-sub{color:var(--white)}
.footer-rule{position:absolute;top:102px;left:58px;width:714px;height:1px;background:rgba(255,255,255,.3)}
.footer-nav{position:absolute;top:120px;left:0;width:830px;display:flex;justify-content:center;gap:14px;
  font-family:'Cinzel',serif;font-size:9.5px}
.footer-nav a{color:var(--white);text-decoration:none}
.footer-nav span{color:var(--white)}
.copyright{position:absolute;top:151px;left:0;width:830px;text-align:center;font-size:8px}
</style>
</head>
<body>
<div class="page">
  <header class="site-header">
    <div class="brand">
      <span class="brand-mark"></span>
      <span class="brand-name">MAPLECREST COVE</span>
      <span class="brand-sub">RETREAT</span>
    </div>
    <nav class="main-nav">
      <a href="#">HOME</a><a href="#">ABOUT US</a><a href="#">PACKAGES</a><a href="#">PRICING</a><a href="#">GALLERY</a><a href="#">WHAT MAKES US UNIQUE</a><a href="#">CONTACT US</a>
    </nav>
  </header>

  <section class="hero">
    <div class="hero-photo" role="img" aria-label="Wedding party posing with the bride and groom under a white arched veranda"></div>
    <h1 class="hero-title">WEDDING &amp; EVENT VENUE</h1>
    <p class="hero-sub">Sed ut perspiciatis unde omnis iste natus error sit voluptatem</p>
    <a class="hero-btn">Read More</a>
  </section>

  <section class="welcome">
    <div class="welcome-heading"><span class="rule"></span><h2>WELCOME TO MAPLECREST COVE</h2><span class="rule"></span></div>
    <div class="ornament" role="img" aria-label="Gold scroll ornament with grape clusters"></div>
    <div class="col col-left">
      <p>Sed ut perspiciatis unde omnis iste natus error sit voluptatem accusantium doloremque laudantium, totam rem aperiam, eaque ipsa quae ab illo inventore veritatis et quasi archit ecto beatae vitae dicta sunt explicabo. Nemo enim ipsam voluptatem quia voluptas sit aspe rnatur aut odit aut fugit, sed quia consequuntur magni dolores eos qui ratione voluptatem sequi nesciunt. Neque porro quisquam est, qui dolorem ipsum quia dolor sit amet, consec tetur, adipisci velit, sed quia non numquam eius modi tempora incidunt</p>
      <p>Sed ut perspiciatis unde omnis iste natus error sit voluptatem accusantium doloremque laudantium, totam rem aperiam, eaque ipsa quae ab illo inventore veritatis et quasi archit ecto beatae vitae dicta sunt explicabo. Nemo enim ipsam voluptatem quia voluptas sit aspe rnatur aut odit aut fugit, sed quia consequuntur magni dolores eos qui ratione voluptatem sequi nesciunt. Neque porro quisquam est, qui dolorem ipsum quia dolor sit amet, consec tetur, adipisci velit, sed quia non numquam eius modi tempora incidunt</p>
      <p>Sed ut perspiciatis unde omnis iste natus error sit voluptatem accusantium doloremque laudantium, totam rem aperiam, eaque ipsa quae ab illo inventore veritatis et quasi archit ecto beatae vitae dicta sunt explicabo. Nemo enim ipsam voluptatem</p>
    </div>
    <div class="col col-right">
      <p>Sed ut perspiciatis unde omnis iste natus error sit voluptatem accusantium doloremque laudantium, totam rem aperiam, eaque ipsa quae ab illo inventore veritatis et quasi archit ecto beatae vitae dicta sunt explicabo. Nemo enim ipsam voluptatem quia voluptas sit aspe rnatur aut odit aut fugit, sed quia consequuntur magni dolores eos qui ratione voluptatem sequi nesciunt. Neque porro quisquam est, qui dolorem ipsum quia dolor sit amet, consec tetur, adipisci velit, sed quia non numquam eius modi tempora incidunt</p>
      <p>Sed ut perspiciatis unde omnis iste natus error sit voluptatem accusantium doloremque laudantium, totam rem aperiam, eaque ipsa quae ab illo inventore veritatis et quasi archit ecto beatae vitae dicta sunt explicabo. Nemo enim ipsam voluptatem quia voluptas sit aspe rnatur aut odit aut fugit, sed quia consequuntur magni dolores eos qui ratione voluptatem sequi nesciunt. Neque porro quisquam est, qui dolorem ipsum quia dolor sit amet, consec tetur, adipisci velit, sed quia non numquam eius modi tempora incidunt</p>
      <a class="gold-btn">Read More</a>
    </div>
  </section>

  <footer class="site-footer">
    <div class="footer-brand">
      <span class="brand-mark"></span>
      <span class="brand-name">MAPLECREST COVE</span>
      <span class="brand-sub">RETREAT</span>
    </div>
    <div class="footer-rule"></div>
    <nav class="footer-nav">
      <a href="#">HOME</a><span>|</span><a href="#">ABOUT US</a><span>|</span><a href="#">PACKAGES</a><span>|</span><a href="#">PRICING</a><span>|</span><a href="#">GALLERY</a><span>|</span><a href="#">WHAT MAKES US UNIQUE</a><span>|</span><a href="#">CONTACT US</a>
    </nav>
    <p class="copyright">© Copyright 2017 Maplecrest Cove.All Rights Reserved</p>
  </footer>
</div>
</body>
</html>
```